Vantro cards

I am in the auto motive, transportation business I would like a business card that is Something cool, modern edgy, having to do with car culture. I offer towing service for high and exotic cars. I also provide towing for collisions and car accidents. I offer open and enclosed transport nationwide.

Target Market(s)

Car culture people high end auto collectors

Industry/Entity Type

Towing car carrier

Contact Information for Business Card

My company colors black yellow and silver

Font styles to use
Serif

```html
<!DOCTYPE html>
<html lang="en">
<head>
<meta charset="utf-8">
<title>Vantro Transportation – Business Cards</title>
<link rel="stylesheet" href="https://fonts.googleapis.com/css2?family=Montserrat:wght@400;700&display=swap">
<style>
  :root {
    --stage: #e9e6e1;
    --card: #ffffff;
    --ink: #111111;
    --text: #222222;
    --yellow: #fbe04f;
    --yellow-deep: #f2c94c;
    --silver: #eeeeee;
    --band: #050505;
    --band-text: #e6e6e6;
  }
  * { box-sizing: border-box; margin: 0; padding: 0; }
  html, body { width: 900px; height: 1200px; overflow: hidden; }
  body {
    background: var(--stage);
    font-family: "Montserrat", Arial, sans-serif;
    color: var(--text);
    position: relative;
  }
  .card {
    position: absolute;
    left: 80px;
    width: 742px;
    height: 442px;
    background: var(--card);
    border-radius: 38px;
    overflow: hidden;
  }
  .card--front { top: 131px; }
  .card--back { top: 639px; }

  .brand {
    position: absolute;
    display: flex;
    align-items: center;
    gap: 12px;
    color: var(--ink);
    font-weight: 700;
  }
  .brand__mark {
    width: 18px; height: 18px;
    background: var(--yellow-deep);
    flex: none;
  }
  .brand__name { line-height: 1.05; text-transform: uppercase; }
  .brand__name span { display: block; }
  .card--front .brand { left: 42px; top: 96px; font-size: 30px; }
  .card--front .brand__name span + span { font-size: 15px; letter-spacing: 0.5px; }
  .card--back .brand { left: 50%; top: 140px; transform: translateX(-50%); font-size: 48px; }
  .card--back .brand__mark { width: 26px; height: 26px; }
  .card--back .brand__name span + span { font-size: 23px; letter-spacing: 1px; }

  .motif {
    position: absolute;
    left: 310px; top: 55px;
    width: 432px; height: 255px;
    background: linear-gradient(90deg, rgba(238,238,238,0.9), rgba(244,244,244,0.4));
  }

  .name-tab {
    position: absolute;
    left: 0; top: 269px;
    width: 262px; height: 58px;
  }
  .name-tab svg { position: absolute; inset: 0; }
  .name-tab__name {
    position: absolute; left: 27px; top: 5px;
    font-size: 27px; font-weight: 700; color: var(--ink);
  }
  .name-tab__role {
    position: absolute; left: 26px; top: 38px;
    font-size: 16px; color: var(--ink);
  }

  .contacts {
    position: absolute; left: 28px; top: 352px;
    list-style: none; font-size: 17px; line-height: 22px;
  }
  .contacts li { display: flex; align-items: center; gap: 11px; }
  .contacts svg { width: 14px; height: 14px; flex: none; }

  .address {
    position: absolute; left: 523px; top: 373px;
    font-size: 17px; line-height: 22px; font-style: normal;
  }

  .accent-line {
    position: absolute; left: 0; top: 362px;
    width: 100%; height: 5px; background: var(--yellow);
  }
  .footer-band {
    position: absolute; left: 0; top: 380px;
    width: 100%; height: 62px;
    background: var(--band);
    color: var(--band-text);
    font-size: 17px;
    display: flex; align-items: center; justify-content: center;
    padding-bottom: 8px;
  }
</style>
</head>
<body>

<section class="card card--front">
  <div class="brand">
    <span class="brand__mark"></span>
    <div class="brand__name"><span>Vantro</span><span>Transportation</span></div>
  </div>

  <div class="motif" role="img" aria-label="Faint decorative vehicle motif"></div>

  <div class="name-tab">
    <svg width="262" height="58" viewBox="0 0 262 58" aria-hidden="true">
      <polygon points="0,0 238,0 262,58 0,58" fill="var(--yellow)"/>
    </svg>
    <div class="name-tab__name">Dana Whitlock</div>
    <div class="name-tab__role">Owner</div>
  </div>

  <ul class="contacts">
    <li>
      <svg viewBox="0 0 14 14" aria-hidden="true"><path d="M2 4c0-1.5 1-2 5-2s5 .5 5 2v1H9.5V4h-5v1H2zM3 6h8l1 6H2z" fill="var(--yellow-deep)"/></svg>
      (555) 214-3870
    </li>
    <li>
      <svg viewBox="0 0 14 14" aria-hidden="true"><rect x="1" y="3" width="12" height="8" fill="var(--yellow-deep)"/><path d="M1 3l6 5 6-5" stroke="#fff" stroke-width="1.2" fill="none"/></svg>
      info@vantrotransportation.com
    </li>
    <li>
      <svg viewBox="0 0 14 14" aria-hidden="true"><circle cx="7" cy="7" r="6" fill="var(--yellow-deep)"/><path d="M1 7h12M7 1c-3 3-3 9 0 12M7 1c3 3 3 9 0 12" stroke="#fff" stroke-width="0.9" fill="none"/></svg>
      www.vantrotransportation.com
    </li>
  </ul>

  <address class="address">48 Harbor Road<br>Millbrook, PA 17002</address>
</section>

<section class="card card--back">
  <div class="brand">
    <span class="brand__mark"></span>
    <div class="brand__name"><span>Vantro</span><span>Transportation</span></div>
  </div>
  <div class="accent-line"></div>
  <div class="footer-band">www.vantrotransportation.com</div>
</section>

</body>
</html>
```